Agrarhandel benötigt Homepage
Zielgruppe
Wir sind ein Agrarhandel mit einem Warenumschlagslager im Sinne eines klassischen Einzelhandels und vertreiben Produkte an Landwirte.
Wir vertreiben folgende Hauptproduktgruppen:
Einzelfuttermittel
wie z.B. Sojaexktraktionsschrot. Die einzelnen Produkte könnten z.B. wie die Futtermittel auf folgender Seite dargestellt werden (https://www.kornprobe-beispiel.eu/de/produkt/trelomixan)
Mischfuttermittel
Hier bieten wir unseren Kunden an, individuelles Mischfutter auf Basis unserer Einzelfuttermittel herzustellen.
Weitere Details und weitere Produktbereiche habe ich in einer Powerpoint-Übersicht dargestellt.
Neben diesen Produkten wollen wir uns als Familienunternehmen selbst vorstellen. Zudem betreiben wir in unserer Familie zusätzlich einen Milchviehbetrieb den wir ebenfalls hervorheben möchten, da wir unseren Kunden gegenüber einerseits als Zulieferer aber auch als Kollege auftreten wollen.
Einzelfuttermittel: Hier können wir durch unsere Unabhängigkeit punkten, da wir nicht abhängig von bestimmten Lieferanten sind und dementsprechend unabhängig beraten können. Wir untersuchen im Vergleich zu unseren Wettbewerben die Qualität der Futtermittel bis ins Detail und können daher eine Transparenz bieten, die Konkurrenten in der Regel nicht bieten können. Unser Warenumschlagsplatz mit moderner Technik ermöglicht es uns äußerst kosteneffizient die Waren umschlagen und ausliefern zu können.
Mischfuttermittel: Auf Basis der vorhandenen Einzelfuttermittel stellen wir je nach Kundenwunsch individuelle Mischfutter her. Wir arbeiten mit offenen Deklarationen, sodass unsere Kunden jederzeit nachvollziehen können, ob auch die Einzelfuttermittel verwendet wurden, die sie bestellt haben und keine billigen Ersatzprodukte verwendet wurden.
Zudem sind wir BT und HUPA zertifiziert. Die aktuellen für unser Unternehmen ausgestellten Zertifikate müssen für unsere Kunden als Download zur Verfügung stehen. Statt dem HUPA-Logo bitte das ..
Aufgabenstellung
Wir möchten gerne ein zeitgemäße Homepage, jedoch muss auch berücksichtigt werden, dass unsere Kunden eher konservativ denken.

```html
<!DOCTYPE html>
<html lang="de">
<head>
<meta charset="utf-8">
<title>Talgrund Agrar – Lieferanten</title>
<link href="https://fonts.googleapis.com/css2?family=Inter:wght@400;500;600;700;800&display=swap" rel="stylesheet">
<style>
:root{
  --green:#42621a;
  --amber:#f2a90e;
  --gold:#f2c81f;
  --grey:#dcdcdc;
  --ink:#111;
  --dark:#242424;
  --white:#fff;
  --straw1:#c98d3c;
  --straw2:#e2b466;
}
*{margin:0;padding:0;box-sizing:border-box}
html,body{width:786px;height:1200px;overflow:hidden}
body{font-family:"Inter",sans-serif;background:var(--white);position:relative;color:var(--ink)}
.abs{position:absolute}
.header{left:0;top:0;width:786px;height:75px;background:var(--grey)}
.header-accent{left:0;top:0;width:46px;height:75px;background:var(--amber)}
.header-bar{left:56px;top:0;width:730px;height:75px;background:var(--green)}
.brand{left:88px;top:20px;width:70px;text-align:center;color:var(--amber);font-weight:700;font-size:10px;line-height:12px}
.brand-dot{display:block;width:12px;height:12px;border-radius:50%;background:var(--amber);margin:0 auto 3px}
.nav{left:342px;top:36px;display:flex;gap:10px;font-size:8.5px;font-weight:700;color:var(--white);letter-spacing:.1px}
.nav .active{color:var(--amber)}
.search{left:749px;top:33px}
.band{left:0;top:75px;width:786px;height:7px;background:var(--grey)}
.hero{left:0;top:88px;width:786px;height:234px;background:linear-gradient(100deg,#b47a2e 0%,#d9a85a 35%,#c99447 60%,#9a8a3e 85%,#b9a45a 100%)}
.hero-title{left:319px;top:175px;width:145px;height:45px;border-radius:12px;background:rgba(200,150,110,.75);border-bottom:1px solid #fff;display:flex;align-items:center;justify-content:center;font-size:22px;font-weight:500;color:var(--ink)}
.thumb{top:270px;width:147px;height:100px}
.t1{left:162px;background:linear-gradient(160deg,#f3e2a2,#8aa040 55%,#3d5a1c)}
.t2{left:318px;background:linear-gradient(150deg,#e8a94a,#c9862a 60%,#a05f16)}
.t3{left:473px;background:linear-gradient(180deg,#e7a764,#b07a3c 55%,#6b4a24)}
.cow-deco{left:404px;top:606px;width:382px;height:346px;background:radial-gradient(ellipse at 60% 45%,rgba(200,160,110,.28),rgba(220,190,150,.12) 60%,rgba(255,255,255,0) 80%)}
.heading{color:var(--amber);font-weight:800;font-size:19.5px;letter-spacing:-.2px}
.copy{font-size:13px;line-height:16px;font-weight:500;width:460px}
.footer{left:0;top:952px;width:786px;height:216px;background:var(--dark)}
.foot-brand{left:94px;top:1020px;width:106px;text-align:center;color:var(--amber);font-weight:700;font-size:14px;line-height:17px}
.foot-brand .brand-dot{width:20px;height:20px;margin-bottom:6px}
.divider{top:993px;width:1px;height:94px;background:var(--white)}
.divider::before,.divider::after{content:"";position:absolute;left:-2.5px;width:6px;height:6px;border-radius:50%;background:var(--white)}
.divider::before{top:-3px}.divider::after{bottom:-3px}
.news-title{left:259px;top:996px;color:var(--white);font-weight:600;font-size:12.5px}
.news-title b{font-size:17px;font-weight:700}
.field{background:var(--grey);height:15px;font-size:6px;font-weight:500;color:#333;padding:4px 6px}
.send{left:444px;top:1054px;width:83px;height:14px;border-radius:4px;background:var(--gold);font-size:7px;font-weight:700;display:flex;align-items:center;justify-content:center}
.contact{left:574px;top:1026px;color:var(--white);font-size:7px;line-height:12px}
.contact li{list-style:none;display:flex;align-items:center;gap:6px}
.reach{left:298px;top:1098px;font-size:13px;font-weight:700;color:var(--amber)}
.reach span{color:var(--white)}
.chat{left:469px;top:1091px;width:33px;height:33px;border-radius:50%;background:#2fb344}
.socials{left:364px;top:1143px;display:flex;gap:3px}
.socials i{display:block;width:12px;height:12px;border-radius:3px;background:var(--white)}
.copyright{left:0;top:1168px;width:786px;height:32px;background:var(--gold);display:flex;align-items:center;justify-content:center;font-size:7px;font-weight:600}
</style>
</head>
<body>
<header class="abs header"></header>
<div class="abs header-accent"></div>
<div class="abs header-bar"></div>
<div class="abs brand"><span class="brand-dot"></span>Talgrund<br>Agrar</div>
<nav class="abs nav"><span class="active">LANDWIRT</span><span>GESCHÄFTSPARTNER</span><span>LIEFERANTEN</span><span>PRODUKTE</span><span>FIRMENPRÄSENTATION</span></nav>
<svg class="abs search" width="16" height="16" viewBox="0 0 16 16"><circle cx="6.5" cy="6.5" r="5" fill="none" stroke="#fff" stroke-width="1.4"/><line x1="10" y1="10" x2="15" y2="15" stroke="#fff" stroke-width="1.6"/></svg>
<div class="abs band"></div>

<section class="abs hero" role="img" aria-label="Strohballen auf einem Feld vor hügeliger Landschaft"></section>
<h1 class="abs hero-title">Lieferanten</h1>
<div class="abs thumb t1" role="img" aria-label="Getreidehalm im Gegenlicht der Sonne"></div>
<div class="abs thumb t2" role="img" aria-label="Goldene Weizenähren"></div>
<div class="abs thumb t3" role="img" aria-label="Mähdrescher bei der Ernte im Weizenfeld"></div>

<div class="abs cow-deco" role="img" aria-label="Blasse Kuhillustration mit Ährenkranz als Hintergrund"></div>

<h2 class="abs heading" style="left:160px;top:418px">Lorem ipsum dolor sit amet</h2>
<p class="abs copy" style="left:164px;top:462px">Ut enim ad minim veniam, quis nostrud exercitation ullamco laboris nisi ut aliquip ex ea Ut enim ad minim veniam, quis nostrud exercitation ullamco laboris nisi ut aliquip ex ea commodo coUt enim ad minim veniam, quis nostrud exercitation ullamco laboris nisi ut aliquip ex ea commodo co con.</p>
<h2 class="abs heading" style="left:166px;top:570px">Duis aute irure dolor in reprehenderit</h2>
<p class="abs copy" style="left:164px;top:614px">Ut enim ad minim veniam, quis nostrud exercitation ullamco laboris nisi ut aliquip ex ea Ut enim ad minim veniam, quis nostrud exercitation ullamco laboris nisi ut aliquip ex ea commodo coUt enim ad minim veniam, quis nostrud exercitation ullamco laboris nisi ut aliquip ex ea commodo co con.</p>
<h2 class="abs heading" style="left:171px;top:733px">Nemo enim ipsam voluptatem quia</h2>
<p class="abs copy" style="left:164px;top:776px;width:515px">Lorem ipsum dolor sit amet, consectetur adipiscing elit, sed do eiusmod tempor incididunt ut labore Lorem ipsum dolor sit amet, consectetur adipiscing elit, sed do eiusmod tempor incididunt ut labore Lorem ipsum dolor sit amet, consectetur adipiscing elit, sed do eiusmod tempor incididunt ut labore</p>

<footer class="abs footer"></footer>
<div class="abs foot-brand"><span class="brand-dot"></span>Talgrund<br>Agrar</div>
<div class="abs divider" style="left:234px"></div>
<div class="abs divider" style="left:552px"></div>
<h3 class="abs news-title">Abonnieren Sie Unseren <b>Newsletter</b></h3>
<div class="abs field" style="left:259px;top:1021px;width:83px">Name</div>
<div class="abs field" style="left:352px;top:1021px;width:83px">Email</div>
<div class="abs field" style="left:444px;top:1021px;width:83px">Telefonnummer</div>
<div class="abs field" style="left:259px;top:1047px;width:176px;height:21px;padding-top:7px">Nachricht</div>
<div class="abs send">SCHICKEN</div>
<ul class="abs contact">
  <li><svg width="6" height="8" viewBox="0 0 6 8"><path d="M3 0a3 3 0 0 1 3 3c0 2-3 5-3 5S0 5 0 3a3 3 0 0 1 3-3z" fill="#fff"/><circle cx="3" cy="3" r="1" fill="#242424"/></svg>Locatins</li>
  <li><svg width="7" height="7" viewBox="0 0 8 8"><circle cx="4" cy="4" r="3.6" fill="#fff"/><path d="M2.6 2.2l.8.9-.4.6c.3.6.7 1 1.3 1.3l.6-.4.9.8-.5.7C3.6 6 2 4.4 1.9 2.7z" fill="#242424"/></svg>+49 7361 482930</li>
  <li><svg width="7" height="6" viewBox="0 0 8 6"><rect width="8" height="6" fill="#fff"/><path d="M0 0l4 3 4-3" fill="none" stroke="#242424" stroke-width=".8"/></svg>info@talgrund-agrar.de</li>
</ul>
<p class="abs reach">Kontaktieren Sie Uns <span>per</span></p>
<div class="abs chat"></div>
<div class="abs socials"><i></i><i></i><i></i><i></i></div>
<div class="abs copyright">Copyright 2023 All Right Reserved</div>
</body>
</html>
```